Veldmark Supplies Business Card

Professional business card that stand out to our potential customers. Front and back with clean modern design

Industry/Entity Type

Oil and gas

Contact Information for Business Card

Name, address, website , office phone and cell number

Requirements
Must have
• Editable files for each employee

```html
<!DOCTYPE html>
<html lang="en">
<head>
<meta charset="utf-8">
<title>Veldmark Supplies Business Card</title>
<link href="https://fonts.googleapis.com/css2?family=Montserrat:wght@400;500;800&display=swap" rel="stylesheet">
<style>
  :root {
    --stage: #e6e7e9;
    --brand-blue: #0fb0d3;
    --brand-red: #e8202a;
    --ink: #1a1a1a;
    --paper: #ffffff;
  }
  * { box-sizing: border-box; margin: 0; padding: 0; }
  html, body { width: 1200px; height: 689px; overflow: hidden; }
  body {
    background: var(--stage);
    font-family: "Montserrat", sans-serif;
    position: relative;
  }
  .card {
    position: absolute;
    top: 190px;
    width: 540px;
    height: 309px;
    border-radius: 18px;
    box-shadow: 0 8px 24px rgba(0,0,0,0.18);
    overflow: hidden;
  }
  .card-front { left: 40px; background: var(--brand-blue); }
  .card-back { left: 620px; background: var(--paper); }

  .wordmark {
    position: absolute;
    display: flex;
    align-items: center;
    gap: 12px;
    font-weight: 800;
    text-transform: uppercase;
    letter-spacing: 1px;
    white-space: nowrap;
  }
  .wordmark-square { display: block; flex: none; }
  .card-front .wordmark {
    left: 50%; top: 50%;
    transform: translate(-50%, -50%);
    color: var(--paper);
    font-size: 30px;
  }
  .card-front .wordmark-square { width: 30px; height: 30px; background: var(--paper); }

  .card-back .wordmark {
    left: 22px; top: 50%;
    transform: translateY(-50%);
    color: var(--brand-red);
    font-size: 15px;
    letter-spacing: 0.5px;
    gap: 8px;
  }
  .card-back .wordmark-square { width: 15px; height: 15px; background: var(--brand-blue); }

  .divider-lines {
    position: absolute;
    left: 262px; top: 40px;
    width: 56px; height: 230px;
  }

  .contact-block {
    position: absolute;
    left: 324px; top: 46px;
    color: var(--ink);
  }
  .person-name {
    color: var(--brand-red);
    font-weight: 800;
    font-size: 21px;
    letter-spacing: 0.5px;
    line-height: 1.1;
  }
  .person-title { font-size: 12px; font-weight: 500; margin-top: 2px; }
  .address { font-size: 11px; line-height: 1.35; margin-top: 10px; }
  .contact-list { list-style: none; margin-top: 10px; }
  .contact-list li {
    display: flex; align-items: center; gap: 8px;
    font-size: 11px; line-height: 1; margin-top: 7px;
  }
  .contact-icon {
    width: 16px; height: 16px; flex: none;
    background: var(--brand-red);
    display: flex; align-items: center; justify-content: center;
  }
  .contact-icon svg { width: 11px; height: 11px; }
  .contact-text { white-space: nowrap; }
  .web-accent { color: var(--brand-red); }
</style>
</head>
<body>

  <section class="card card-front" aria-label="Card front">
    <div class="wordmark"><span class="wordmark-square"></span>Veldmark Supplies</div>
  </section>

  <section class="card card-back" aria-label="Card back">
    <div class="wordmark"><span class="wordmark-square"></span>Veldmark Supplies</div>

    <svg class="divider-lines" viewBox="0 0 56 230" aria-hidden="true">
      <line x1="16" y1="0" x2="46" y2="230" stroke="#0fb0d3" stroke-width="1.2"/>
      <line x1="30" y1="20" x2="52" y2="200" stroke="#e8202a" stroke-width="1.2"/>
      <line x1="2" y1="40" x2="26" y2="220" stroke="#e8202a" stroke-width="1.2"/>
    </svg>

    <div class="contact-block">
      <h1 class="person-name">DALE HARROW</h1>
      <p class="person-title">President</p>
      <p class="address">482 Cedar Ridge Rd, Ste<br>210, Midvale, TX 79701</p>
      <ul class="contact-list">
        <li>
          <span class="contact-icon">
            <svg viewBox="0 0 12 12"><path d="M2 1h2l1 3-1.3 1a6 6 0 0 0 3.3 3.3L8 7l3 1v2a1 1 0 0 1-1 1A9 9 0 0 1 1 2a1 1 0 0 1 1-1z" fill="#fff"/></svg>
          </span><span class="contact-text">432-555-0148</span>
        </li>
        <li>
          <span class="contact-icon">
            <svg viewBox="0 0 12 12"><rect x="3" y="0.5" width="6" height="11" rx="1" fill="none" stroke="#fff" stroke-width="1.2"/><circle cx="6" cy="9.5" r="0.7" fill="#fff"/></svg>
          </span><span class="contact-text">432-555-0193</span>
        </li>
        <li>
          <span class="contact-icon">
            <svg viewBox="0 0 12 12"><rect x="1" y="2.5" width="10" height="7" fill="none" stroke="#fff" stroke-width="1.1"/><path d="M1 2.5l5 4 5-4" fill="none" stroke="#fff" stroke-width="1.1"/></svg>
          </span><span class="contact-text">info@veldmarksupplies.com</span>
        </li>
        <li>
          <span class="contact-icon">
            <svg viewBox="0 0 12 12"><circle cx="6" cy="6" r="4.8" fill="none" stroke="#fff" stroke-width="1.1"/><ellipse cx="6" cy="6" rx="2" ry="4.8" fill="none" stroke="#fff" stroke-width="1"/><line x1="1.2" y1="6" x2="10.8" y2="6" stroke="#fff" stroke-width="1"/></svg>
          </span><span class="contact-text">www.<span class="web-accent">veldmarksupplies</span>.com</span>
        </li>
      </ul>
    </div>
  </section>

</body>
</html>
```